Bench Advertisement - We Buy Houses Design Needed

Need a catchy, simple but elegant design for bus benches to advertise our company.

We need our website, or phone number, and a smal description (1-2 bulletpoints of what we do and what we offer)

The tricky part is for the designer to fit everything and make the website name as part of the title and fitting everything so that people passing by on the street can see what we offer.

Our website is quickdealhomebuyer.com - (916) 555-0143

Something simple but something that catches the eye of walking pedestrians, and drivers driving by the bench.

Our company buys houses, any condition, any situation, we buy houses for cash and close quickly. You can use this description to create a few bulletpoints however you like. Must follow dimensions in attachment.

Target Market(s)

People in foreclosure, about to lose their homes, people that need a quick cash sale of their property

Industry/Entity Type

Real Estate

Requirements
Must have
• catchy, website name, phone number, few brief bulletpoints about what we offer, colors that will catch peoples eye while walking or driving - advertisement will be placed on bus benches - visit our website to see the type of houses we buy - Also have more work for winner of design with possible bonuses
Nice to have
• Feel free to use description or images on our website - make sure the description is just bullet points and it fits with the overall theme / size of the advertisement - Bold bright colors - put yourself in their shoes (if you were going through financial difficulties and about to lose your house to foreclosure or auction, what would you want to see to pick up the phone and call us for a quick sale of your house?) (or if you have a house that you are having a problem with, problem renters, unkept/beat up house, what would make you want to call us and sell your house to us?)

```html
<!DOCTYPE html>
<html lang="en">
<head>
<meta charset="utf-8">
<title>Quick Deal Home Buyer – Bench Advertisement</title>
<link rel="stylesheet" href="https://fonts.googleapis.com/css2?family=Roboto+Condensed:wght@400;700&family=Open+Sans:wght@400&display=swap">
<style>
  :root {
    --brand-red: #e0040a;
    --brand-red-deep: #c80008;
    --panel-light: #f4f4f4;
    --panel-shade: #dcdcdc;
    --ink-grey: #6b6b6b;
    --ink-dark: #333333;
    --backdrop: #e9e6e3;
  }
  html, body {
    margin: 0;
    width: 1200px;
    height: 1061px;
    overflow: hidden;
    background: var(--backdrop);
  }
  .bench-ad {
    position: absolute;
    left: 40px;
    top: 270px;
    width: 1120px;
    height: 520px;
    display: flex;
    flex-direction: column;
    box-shadow: 0 10px 30px rgba(0,0,0,.18);
    font-family: "Roboto Condensed", sans-serif;
  }
  .band-top {
    height: 110px;
    background: linear-gradient(180deg, var(--brand-red), var(--brand-red-deep));
  }
  .band-bottom {
    height: 165px;
    background: linear-gradient(180deg, var(--brand-red-deep), var(--brand-red));
  }
  .message-panel {
    height: 245px;
    position: relative;
    background: linear-gradient(180deg, #ffffff 0%, var(--panel-light) 55%, var(--panel-shade) 100%);
  }
  .house-illustration {
    position: absolute;
    left: 40px;
    top: -10px;
    width: 300px;
    height: 250px;
  }
  .website {
    position: absolute;
    left: 350px;
    top: 4px;
    margin: 0;
    font-weight: 700;
    font-size: 62px;
    line-height: 1;
    color: var(--brand-red);
    letter-spacing: -0.5px;
  }
  .call-prompt {
    position: absolute;
    left: 680px;
    top: 80px;
    margin: 0;
    font-size: 15px;
    color: var(--ink-dark);
  }
  .company-name {
    position: absolute;
    left: 360px;
    top: 112px;
    display: flex;
    align-items: center;
    gap: 8px;
    font-family: "Roboto Condensed", sans-serif;
    font-size: 19px;
    color: var(--ink-dark);
    text-transform: uppercase;
  }
  .company-name .mark {
    width: 14px;
    height: 14px;
    background: var(--brand-red);
  }
  .phone {
    position: absolute;
    left: 680px;
    top: 100px;
    margin: 0;
    font-size: 60px;
    color: var(--ink-grey);
    line-height: 1;
  }
  .offer-list {
    position: absolute;
    left: 370px;
    top: 168px;
    margin: 0;
    padding: 0;
    list-style: none;
    font-size: 30px;
    line-height: 1.15;
    color: var(--ink-grey);
  }
  .offer-list .closing {
    padding-left: 60px;
    display: flex;
    align-items: center;
    gap: 10px;
  }
  .chevron { width: 12px; height: 22px; }
</style>
</head>
<body>
  <section class="bench-ad">
    <div class="band-top"></div>
    <div class="message-panel">
      <svg class="house-illustration" role="img" aria-label="Illustration of a small white house with a red roof and a red for-sale tag hanging from the chimney" viewBox="0 0 300 250">
        <defs>
          <linearGradient id="houseTone" x1="0" y1="0" x2="0" y2="1">
            <stop offset="0" stop-color="#d8262b"/>
            <stop offset="0.45" stop-color="#e6e6e6"/>
            <stop offset="1" stop-color="#b9b2ab"/>
          </linearGradient>
        </defs>
        <rect x="10" y="20" width="280" height="220" rx="20" fill="url(#houseTone)" opacity="0.85"/>
      </svg>

      <h1 class="website">quickdealhomebuyer.com</h1>
      <p class="call-prompt">pick up the phone and call us for a quick sale of your house</p>
      <div class="company-name"><span class="mark"></span>Quick Deal Home Buyer</div>
      <p class="phone">(916) 555-0143</p>

      <ul class="offer-list">
        <li>Our company buys houses, Any condition, Any situation</li>
        <li class="closing">
          <svg class="chevron" viewBox="0 0 12 22"><path d="M0 0 L12 11 L0 22 L4 11 Z" fill="var(--brand-red)"/></svg>
          We buy houses for cash and close quickly
          <svg class="chevron" viewBox="0 0 12 22"><path d="M12 0 L0 11 L12 22 L8 11 Z" fill="var(--brand-red)"/></svg>
        </li>
      </ul>
    </div>
    <div class="band-bottom"></div>
  </section>
</body>
</html>
```